Foot and ankle surgeon requires a website design

I need a website where prospective and established patients can obtain information and then direct them to making appointments. My practice is a highly professional surgical practice specialising in surgery to the foot and ankle. My title is Mr Colin Brasket, Podiatric Foot & Ankle Surgeon. My qualifications are: BSc MSc FACPS
The practice website will require information on: Locations, phone numbers to make appointments, general background on podiatric surgery,
I would like to include information on: my hospital appointments, surgical fellowships held, training programs undertaken, association memberships, publications written, links to useful websites
A page dedicated to common foot conditions would be useful and also a page with referral information including an online registration section that will be sent direct to the receptionist.
Examples of similar websites include:
http://www.dorvelquintaro.com.au/
http://www.haldenfootsurgeon.com.au/
I will provide files on logo, self photos and my personal training history etc.
Also if there is going to be a background theme I personally am associated with surfing and beach activities, it would be great if this was able to be reflected in the design.
Thank you.

```html
<!DOCTYPE html>
<html lang="en">
<head>
<meta charset="utf-8">
<title>Mr Colin Brasket – Podiatric Foot &amp; Ankle Surgeon</title>
<link rel="stylesheet" href="https://fonts.googleapis.com/css2?family=Arimo:ital,wght@0,400;0,700;1,400&family=Open+Sans:wght@400;600&family=Tinos:wght@400;700&family=Ubuntu:wght@300;400&display=swap">
<style>
:root{
  --sea-light:#d9eff5;
  --sea-mid:#a9d9e6;
  --panel:#ebf7fc;
  --navy:#1d3f73;
  --ink:#2b2b2b;
  --grey:#555;
  --orange:#f47a20;
  --blue-1:#3aa9e0;
  --blue-2:#1f88d6;
  --blue-3:#2f56a8;
  --blue-4:#1b3a86;
  --hero-dark:#12417f;
  --hero-light:#2f7cc0;
}
*{margin:0;padding:0;box-sizing:border-box}
html,body{width:872px;height:1200px;overflow:hidden}
body{position:relative;font-family:"Arimo",Arial,sans-serif;color:var(--ink);
  background:linear-gradient(160deg,var(--sea-light) 0%,var(--sea-mid) 45%,#c9e9f1 70%,var(--sea-mid) 100%)}
.abs{position:absolute}
.brand{font-family:"Tinos",serif;font-weight:700;color:var(--navy);font-size:18px;white-space:nowrap}
.brand-dot{width:14px;height:14px;border-radius:50%;background:var(--orange);display:inline-block;margin-right:8px;vertical-align:-1px}
.brand-sub{font-family:"Tinos",serif;font-size:9px;color:var(--orange);margin-left:22px;margin-top:2px}
.contact-top{right:82px;font-size:12px;color:var(--navy);text-align:right;display:flex;align-items:center;gap:6px}
.nav{left:298px;top:72px;width:502px;height:32px;background:var(--orange);
  clip-path:polygon(32px 0,100% 0,100% 100%,0 100%)}
.nav a{position:absolute;top:10px;font-family:"Open Sans",sans-serif;font-size:9.6px;color:#fff;text-decoration:none;white-space:nowrap}
.hero{left:72px;top:104px;width:728px;height:328px;
  background:radial-gradient(ellipse at 68% 55%,#8fd0f5 0%,var(--hero-light) 30%,var(--hero-dark) 75%)}
.hero-name{left:402px;top:186px;font-family:"Tinos",serif;font-weight:700;color:#fff;font-size:25px}
.hero-sub{left:402px;top:215px;font-family:"Tinos",serif;color:#fff;font-size:13px}
.panel{left:72px;top:432px;width:728px;height:585px;background:var(--panel)}
.intro{left:88px;top:456px;width:455px;font-family:"Tinos",serif;font-size:14.5px;line-height:17.6px;color:var(--navy)}
.body-copy{left:89px;top:522px;width:450px;font-size:9.6px;line-height:17.6px;color:var(--ink)}
.body-copy p{margin-bottom:17.6px}
.tile{left:596px;width:186px;height:66px;color:#fff;border:2px solid #fff;box-shadow:0 4px 4px rgba(0,0,0,.12)}
.tile .t1{position:absolute;left:12px;font-size:12px}
.tile .t2{position:absolute;left:12px;font-size:13px;font-weight:700;letter-spacing:.5px}
.tile svg{position:absolute;right:8px;top:6px}
.h2{font-family:"Tinos",serif;font-size:24px;color:var(--ink)}
.conditions{left:89px;top:828px;width:284px;list-style:none}
.conditions li{height:27.6px;line-height:27.6px;font-size:10.4px;padding-left:18px;position:relative}
.conditions li::before{content:"";position:absolute;left:7px;top:11px;border-left:5px solid #999;border-top:3px solid transparent;border-bottom:3px solid transparent}
.conditions li.active{background:#d6edf7;border-left:3px solid var(--orange);padding-left:15px}
.conditions li.active::before{left:5px;border-left-color:#333}
.quote{left:458px;top:826px;width:316px;font-size:9.4px;line-height:16px;color:#555}
.qmark{font-family:"Tinos",serif;font-size:22px;color:#777;line-height:0}
.author{left:620px;top:927px;font-size:9.6px;font-style:italic;color:var(--navy)}
.avatar{left:694px;top:904px;width:62px;height:62px;border-radius:50%;border:2px solid #fff;
  background:radial-gradient(circle,#8a6a55 0%,#3a3a3a 100%);box-shadow:0 1px 4px rgba(0,0,0,.3)}
.divider{top:1035px;height:150px;border-left:1px dotted #8aa}
.foot-h{font-size:12px;color:#333;font-family:"Ubuntu",sans-serif}
.foot-lines{font-family:"Ubuntu",sans-serif;font-weight:300;font-size:10px;line-height:17.5px;color:#333}
.map{left:577px;top:1064px;width:218px;height:96px;border:3px solid #cfd6d8;
  background:linear-gradient(135deg,#eef0e6 0%,#e6eadb 40%,#d8e6c6 60%,#e9ebe2 100%)}
.copyright{left:80px;top:1151px;font-size:10px;color:#333}
</style>
</head>
<body>

<header>
  <div class="abs" style="left:78px;top:44px">
    <div class="brand"><span class="brand-dot"></span>Mr Colin Brasket</div>
    <div class="brand-sub">Podiatric Foot &amp; Ankle Surgeon</div>
  </div>
  <div class="abs contact-top" style="top:26px">Call Us : 08 9471 2086
    <svg width="11" height="18" viewBox="0 0 11 18"><rect x="1" y="1" width="9" height="16" rx="1.5" fill="none" stroke="#222" stroke-width="1.6"/><line x1="4" y1="14.5" x2="7" y2="14.5" stroke="#222" stroke-width="1.2"/></svg>
  </div>
  <div class="abs contact-top" style="top:49px">27 Sandbar Coastal Drive
    <svg width="12" height="18" viewBox="0 0 12 18"><path d="M6 1a5 5 0 0 1 5 5c0 4-5 11-5 11S1 10 1 6a5 5 0 0 1 5-5z" fill="#222"/><circle cx="6" cy="6" r="2" fill="#fff"/></svg>
  </div>
  <nav class="abs nav">
    <a style="left:43px">Home</a>
    <a style="left:87px">About Us</a>
    <a style="left:147px">Foot Conditions</a>
    <a style="left:237px">Treatments</a>
    <a style="left:306px">Surgery</a>
    <a style="left:359px">Employment</a>
    <a style="left:435px">Our Locations</a>
  </nav>
</header>

<section class="abs hero" role="img" aria-label="Portrait of the surgeon in a white coat holding a clipboard beside a glowing blue X-ray of a foot"></section>
<div class="abs hero-name">Mr Colin Brasket</div>
<div class="abs hero-sub">Podiatric Foot &amp; Ankle Surgeon</div>

<main>
  <div class="abs panel"></div>
  <h1 class="abs intro" style="font-weight:400">The Shoreline Foot Health Group strive to provide exceptional service and care to all patients, young and old, to ensure they enjoy a pain free lifestyle.</h1>
  <div class="abs body-copy">
    <p>For those unfamiliar with our services, we are a team of accredited health professionals dealing with the prevention, diagnosis, treatment and rehabilitation of medical and surgical conditions related to feet, ankles and lower limbs.</p>
    <p>The Shoreline Foot Health Group have practices based throughout regional Western Australia in Geraldton and Kalgoorlie and offer the following services; sports injuries, foot care, foot orthoses and diabetes care.</p>
    <p>Many foot and lower limb problems, if identified early can be prevented, so take the right step and contact the Shoreline Foot Health Group for advice on your foot, ankle, heel or leg pain or sports injury.</p>
  </div>

  <div class="abs tile" style="top:450px;background:var(--blue-1)">
    <span class="t1" style="top:18px">MY HOPITAL</span><span class="t2" style="top:35px">APPOINTMENT</span>
    <svg width="50" height="50" viewBox="0 0 50 50"><circle cx="22" cy="22" r="19" fill="#f4f4f4" stroke="#444" stroke-width="3"/><path d="M22 10v12h9" stroke="#333" stroke-width="2" fill="none"/><rect x="33" y="30" width="6" height="18" fill="#4cae3a"/><rect x="27" y="36" width="18" height="6" fill="#4cae3a"/></svg>
  </div>
  <div class="abs tile" style="top:528px;background:var(--blue-2)">
    <span class="t1" style="top:26px">SURGICAL</span><span class="t2" style="top:43px">FELLOWSHIPS HELD</span>
    <svg width="44" height="40" viewBox="0 0 44 40"><rect x="14" y="2" width="5" height="15" fill="var(--orange)"/><rect x="9" y="7" width="15" height="5" fill="var(--orange)"/><path d="M3 14v24M41 24v14M3 32h38" stroke="#fff" stroke-width="3" fill="none"/><rect x="6" y="24" width="34" height="6" rx="2" fill="#fff"/><ellipse cx="34" cy="21" rx="5" ry="3" fill="#fff"/></svg>
  </div>
  <div class="abs tile" style="top:606px;background:var(--blue-3)">
    <span class="t1" style="top:24px">TRAINING</span><span class="t2" style="top:38px">PROGRAMS</span>
    <svg width="40" height="40" viewBox="0 0 40 40"><rect x="14" y="2" width="12" height="36" fill="#fff"/><rect x="2" y="14" width="36" height="12" fill="#fff"/></svg>
  </div>
  <div class="abs tile" style="top:685px;background:var(--blue-4)">
    <span class="t1" style="top:22px">ASSOCIATION</span><span class="t2" style="top:36px">MEMBERSHIPS</span>
    <svg width="42" height="42" viewBox="0 0 42 42"><circle cx="21" cy="19" r="14" fill="none" stroke="#fff" stroke-width="2"/><circle cx="21" cy="8" r="4" fill="#fff"/><circle cx="9" cy="24" r="4" fill="#fff"/><circle cx="33" cy="24" r="4" fill="#fff"/><path d="M3 40c0-7 12-7 12 0zM27 40c0-7 12-7 12 0zM15 21c0-6 12-6 12 0z" fill="#fff"/></svg>
  </div>

  <h2 class="abs h2" style="left:88px;top:782px;font-weight:400">Common Foot condition:</h2>
  <ul class="abs conditions">
    <li>Ankle Replacement</li>
    <li class="active">Ankle Trauma</li>
    <li>Tendom Rupture</li>
    <li>Heel Pain</li>
    <li>Sports Medicine Services</li>
  </ul>

  <h2 class="abs h2" style="left:460px;top:782px;font-weight:400">Testimonials</h2>
  <p class="abs quote"><span class="qmark">&#8220;</span> Lorem ipsum dolor sit amet, consectetur adipisicing elit, sed do eiusmod tempor incididunt ut labore et dolore magna aliqua. Ut enim ad derit in voluptate velit esse cillum dolore eu fugiat nulla pariatur. Excepteur sint occaecat cupidatat non proident, sunt in culpa qui officia deserunt mollitut aliquip ex ea commodo consequat. ..... <span class="qmark">&#8221;</span></p>
  <div class="abs author">Mr Darren Holt</div>
  <div class="abs avatar" role="img" aria-label="Portrait photo of the patient giving the testimonial"></div>
</main>

<footer>
  <div class="abs" style="left:96px;top:1078px">
    <div class="brand"><span class="brand-dot"></span>Mr Colin Brasket</div>
    <div class="brand-sub">Podiatric Foot &amp; Ankle Surgeon</div>
  </div>
  <div class="abs copyright">Copyright © 2014 Mr Colin Brasket. All rights reserved.</div>
  <div class="abs divider" style="left:343px"></div>
  <div class="abs divider" style="left:553px"></div>
  <div class="abs foot-h" style="left:381px;top:1039px">Contact Info</div>
  <div class="abs foot-lines" style="left:382px;top:1063px">27 Sandbar Coastal<br>Drive<br>PO Box 3820,<br>Marlin Bay WA 6531<br>Phone: 08 9471 2086<br>Fax: 08 9310 5527</div>
  <div class="abs foot-h" style="left:577px;top:1039px">Find Us</div>
  <div class="abs map" role="img" aria-label="Street map showing the practice location"></div>
</footer>

</body>
</html>
```